Business cards to launch an education platform

Hi,
I am looking at having new business cards designed.
I am a startup, developing a web platform for schools and university, the education world. It's an online assessment system.
I would like a card that looks classy, and that is using the colors and the font of my logo.

I have attached:
1) my logo
2) A business card that I have designed quickly so you can have all the information required in the card, but I really don't like it.
3) The font that I am using (Lato Regular) to design my web platform
4) Some screenshots of my web platform so you can have a look at the style that I have.

Target Market(s)

Major market: Education system: Schools and university
Minor markets: Business in general

Industry/Entity Type

Business

Contact Information for Business Card

Clara Fenwick
Director

M: 0437 518 902
E: clara.fenwick@amberLoomSystems.com.au

Requirements
Must have
• The colors of my logo

```html
<!DOCTYPE html>
<html lang="en">
<head>
<meta charset="UTF-8">
<title>Amber Loom Systems – Business Card</title>
<link href="https://fonts.googleapis.com/css2?family=Lato:wght@400;700&display=swap" rel="stylesheet">
<style>
  :root {
    --page-bg: #e4e6e8;
    --blue-light: #3cbfe9;
    --blue-mid: #1f8fd4;
    --blue-deep: #1273c0;
    --blue-navy: #1b4f8e;
    --white: #ffffff;
    --card-shadow: rgba(20, 40, 70, 0.22);
  }
  * { margin: 0; padding: 0; box-sizing: border-box; }
  html, body {
    width: 1200px;
    height: 900px;
    overflow: hidden;
    background: var(--page-bg);
    font-family: "Lato", sans-serif;
  }
  .canvas {
    width: 1200px;
    height: 900px;
    display: flex;
    flex-direction: column;
    align-items: center;
    justify-content: center;
    gap: 60px;
  }
  .card {
    position: relative;
    width: 600px;
    height: 360px;
    overflow: hidden;
    box-shadow: 0 10px 28px var(--card-shadow);
  }

  /* Back of card */
  .card-back {
    background: linear-gradient(180deg, var(--blue-light) 0%, var(--blue-mid) 45%, var(--blue-deep) 100%);
    display: flex;
    align-items: center;
    justify-content: center;
    gap: 18px;
  }
  .card-back .brand-mark {
    width: 34px;
    height: 34px;
    background: var(--white);
  }
  .card-back .brand-name {
    color: var(--white);
    font-size: 40px;
    font-weight: 400;
    letter-spacing: 2px;
  }

  /* Front of card */
  .card-front { background: var(--white); }
  .card-front .waves {
    position: absolute;
    inset: 0;
    width: 100%;
    height: 100%;
  }
  .brand-lockup {
    position: absolute;
    top: 52px;
    left: 150px;
    display: flex;
    align-items: center;
    gap: 14px;
  }
  .brand-lockup .brand-mark {
    width: 40px;
    height: 40px;
    background: var(--blue-deep);
  }
  .brand-lockup .brand-name {
    color: var(--blue-navy);
    font-size: 30px;
    font-weight: 400;
    letter-spacing: 2px;
  }
  .contact {
    position: absolute;
    left: 0;
    right: 0;
    top: 218px;
    text-align: center;
    color: var(--white);
    padding-left: 60px;
  }
  .contact .name {
    font-size: 22px;
    font-weight: 400;
    line-height: 1.1;
  }
  .contact .role {
    font-size: 14px;
    margin-bottom: 12px;
  }
  .contact .line {
    display: flex;
    align-items: center;
    justify-content: center;
    gap: 8px;
    font-size: 16px;
    line-height: 1.5;
  }
  .contact .icon { width: 13px; height: 13px; fill: var(--white); }
</style>
</head>
<body>
<main class="canvas">

  <section class="card card-back" aria-label="Card back">
    <span class="brand-mark"></span>
    <span class="brand-name">Amber Loom Systems</span>
  </section>

  <section class="card card-front" aria-label="Card front">
    <svg class="waves" viewBox="0 0 600 360" preserveAspectRatio="none" aria-hidden="true">
      <defs>
        <linearGradient id="front-blue" x1="0" y1="0" x2="0" y2="1">
          <stop offset="0" stop-color="#2fb2e4"/>
          <stop offset="1" stop-color="#1273c0"/>
        </linearGradient>
      </defs>
      <path d="M0 80 C 120 150, 300 230, 600 190 L600 360 L0 360 Z" fill="url(#front-blue)"/>
      <path d="M0 92 C 140 170, 320 240, 600 200 L600 212 C 330 250, 140 190, 0 108 Z" fill="#ffffff"/>
      <path d="M150 130 C 260 200, 420 225, 600 178 L600 188 C 420 232, 270 210, 150 130 Z" fill="#1b63b0"/>
    </svg>

    <div class="brand-lockup">
      <span class="brand-mark"></span>
      <span class="brand-name">Amber Loom Systems</span>
    </div>

    <div class="contact">
      <p class="name">Clara Fenwick</p>
      <p class="role">Director</p>
      <p class="line">
        <svg class="icon" viewBox="0 0 24 24" aria-hidden="true"><path d="M6.6 10.8a15.1 15.1 0 0 0 6.6 6.6l2.2-2.2a1 1 0 0 1 1-.25 11.4 11.4 0 0 0 3.6.57 1 1 0 0 1 1 1V20a1 1 0 0 1-1 1A17 17 0 0 1 3 4a1 1 0 0 1 1-1h3.5a1 1 0 0 1 1 1c0 1.25.2 2.45.57 3.57a1 1 0 0 1-.25 1z"/></svg>
        <span>0437 518 902</span>
      </p>
      <p class="line">
        <svg class="icon" viewBox="0 0 24 24" aria-hidden="true"><path d="M2 5h20v14H2z M3.5 6.5 12 13l8.5-6.5" fill="none" stroke="#ffffff" stroke-width="2"/></svg>
        <span>clara.fenwick@amberLoomSystems.com.au</span>
      </p>
    </div>
  </section>

</main>
</body>
</html>
```